Pepper & Palm Business Card FUN & EXCITING

Here is the Information for the Card:
Jaswinder Bains (Ravi)
E: RaviBains@postlark.com
C: (480) 555-0147
www.PepperPalmLV.com

We don't want traditional Indian cliche, We a playful bold and fun business card.

Files: https://files.cloudvessel.net/share/folders/7TqRmXpZ2vKa9LwBn4YcHd3JsEf6UoGi?usp=share_link

https://files.cloudvessel.net/share/folders/4MzXaQ8rTw2YbNcVk6PsLe5GhJdR3FoU?usp=share_link

Target Market(s)

Las Vegas Local Restaurant

Industry/Entity Type

Indian Restaurant

Contact Information for Business Card

Name, Email, Cell Phone, Company Logo

```html
<!DOCTYPE html>
<html lang="en">
<head>
<meta charset="utf-8">
<title>Pepper &amp; Palm Business Card</title>
<link href="https://fonts.googleapis.com/css2?family=Montserrat:wght@400;600;800&display=swap" rel="stylesheet">
<style>
  :root {
    --backdrop: #2f2f2f;
    --card: #000000;
    --accent: #f07a1f;
    --ink: #ffffff;
    --cream: #efe6cc;
  }
  * { margin: 0; padding: 0; box-sizing: border-box; }
  html, body { width: 1200px; height: 1108px; overflow: hidden; }
  body {
    background: var(--backdrop);
    font-family: "Montserrat", sans-serif;
    color: var(--ink);
    position: relative;
  }
  .card {
    position: absolute;
    left: 262px;
    width: 708px;
    height: 432px;
    background: var(--card);
    border-radius: 22px;
    border-left: 3px solid var(--accent);
    border-bottom: 3px solid var(--accent);
  }
  .card--front { top: 130px; }
  .card--back { top: 604px; height: 446px; }

  .logo { position: absolute; text-align: center; }
  .logo__name {
    font-weight: 800;
    text-transform: uppercase;
    line-height: 0.9;
    letter-spacing: -1px;
    color: var(--ink);
  }
  .logo__place { font-weight: 600; color: var(--ink); }
  .logo__art {
    margin: 0 auto;
    border-radius: 14px;
    background: linear-gradient(120deg, var(--accent) 0%, var(--cream) 55%, #e86a9a 100%);
  }
  .logo__tagline { color: #cfcfcf; font-weight: 600; }

  .card--front .logo { left: 240px; top: 78px; width: 230px; }
  .card--front .logo__name { font-size: 50px; }
  .card--front .logo__place { font-size: 13px; margin: 6px 0 8px; text-align: right; }
  .card--front .logo__art { width: 200px; height: 104px; }
  .card--front .logo__tagline { font-size: 8px; margin-top: 10px; }

  .card--back .logo { left: 92px; top: 140px; width: 170px; }
  .card--back .logo__name { font-size: 37px; }
  .card--back .logo__place { font-size: 10px; margin: 5px 0 6px; text-align: right; }
  .card--back .logo__art { width: 150px; height: 80px; }
  .card--back .logo__tagline { font-size: 7px; margin-top: 8px; }

  .divider {
    position: absolute;
    left: 318px; top: 140px;
    width: 2px; height: 200px;
    background: var(--accent);
  }
  .contact { position: absolute; left: 335px; top: 138px; }
  .contact__name { font-size: 26px; font-weight: 600; color: var(--accent); line-height: 1.1; }
  .contact__role { font-size: 16px; margin-bottom: 20px; }
  .contact__list { list-style: none; }
  .contact__item {
    display: flex; align-items: center; gap: 12px;
    font-size: 16px; height: 27px;
  }
  .contact__item svg { width: 14px; height: 14px; fill: var(--accent); flex: none; }
  .contact__address { font-size: 16px; line-height: 1.25; margin-top: 14px; }
</style>
</head>
<body>

<section class="card card--front">
  <div class="logo">
    <div class="logo__name">Pepper<br>&amp; Palm</div>
    <div class="logo__place">Las Vegas, NV</div>
    <div class="logo__art" role="img" aria-label="Playful cartoon of a walking curry bowl and flatbread mascot with hearts and sparkles"></div>
    <div class="logo__tagline">"A match made in heaven"</div>
  </div>
</section>

<section class="card card--back">
  <div class="logo">
    <div class="logo__name">Pepper<br>&amp; Palm</div>
    <div class="logo__place">Las Vegas, NV</div>
    <div class="logo__art" role="img" aria-label="Playful cartoon of a walking curry bowl and flatbread mascot with hearts and sparkles"></div>
    <div class="logo__tagline">"A match made in heaven"</div>
  </div>

  <div class="divider"></div>

  <div class="contact">
    <div class="contact__name">Jaswinder Bains (Ravi)</div>
    <div class="contact__role">owner</div>
    <ul class="contact__list">
      <li class="contact__item">
        <svg viewBox="0 0 16 16"><path d="M1 6c0-2 3-3 7-3s7 1 7 3v1h-3V5.5H4V7H1z M3 8h10l1 6H2z"/></svg>
        (480) 555-0147
      </li>
      <li class="contact__item">
        <svg viewBox="0 0 16 16"><path d="M1 3h14v2L8 9 1 5z M1 6.5l7 4 7-4V13H1z"/></svg>
        RaviBains@postlark.com
      </li>
      <li class="contact__item">
        <svg viewBox="0 0 16 16"><circle cx="8" cy="8" r="7"/><path d="M4 5c2 0 2 2 4 2s1 3-1 4-1 3-2 3c-1-2-3-3-2-5s-1-2 1-4z" fill="#000"/></svg>
        www.PepperPalmLV.com
      </li>
    </ul>
    <div class="contact__address">418 Desert Bloom Ave, #112<br>Henderson, NV 89014</div>
  </div>
</section>

</body>
</html>
```